Fundraising campaign to raise money to purchase a pub

We are a voluntary group campaigning to stop a pub from becoming residential flats by fighting planning proposals. We are also raising money to buy or lease the pub to re-open it as a community pub.I have attached a mock idea for a flyer.We are seeking a flyer that we can use to handout.

The purpose of the flyer is to invite people to our public meeting and to complete our pub survey.

We are looking for an A5 flyer in terms of size

Target Market(s)

Local residents, investors

Industry/Entity Type

Residential

Font styles to use
Serif
Sans Serif
Decorative
Script

Requirements
Must have
• Be eyecatching. Must have a summary of the campaign. Must also have website date and time of the public meeting. Must also promote the survey and website. Must also have contact details. Must have the survey. The date and the survey should be easily spotted.
Nice to have
• A picture of the heron
Should not have
• Clip art

```html
<!DOCTYPE html>
<html lang="en">
<head>
<meta charset="utf-8">
<title>Save The Heron – Flyer</title>
<link href="https://fonts.googleapis.com/css2?family=Oswald:wght@600;700&family=Arimo:wght@400;700&display=swap" rel="stylesheet">
<style>
  :root{
    --alarm-red:#c8181e;
    --deep-red:#7b1417;
    --band-red:#b3191d;
    --paper:#f1efec;
    --white:#ffffff;
    --ink:#141414;
    --accent:#ffd27a;
  }
  *{margin:0;padding:0;box-sizing:border-box}
  html,body{width:857px;height:1200px;overflow:hidden;background:var(--paper)}
  .flyer{position:relative;width:857px;height:1200px;background:var(--deep-red);font-family:'Arimo',Arial,sans-serif;color:var(--white);overflow:hidden}
  .alarm{height:92px;background:var(--paper);display:flex;align-items:center;justify-content:center}
  .alarm h1{font-family:'Oswald','Arial Narrow',sans-serif;font-weight:700;font-size:74px;letter-spacing:3px;color:var(--alarm-red);line-height:1}
  .street-photo{position:absolute;top:92px;left:0;width:857px;height:351px;background:linear-gradient(180deg,#5a4c44 0%,#3c2a26 45%,#6a5e58 100%)}
  .headline-box{position:absolute;top:236px;left:334px;width:372px;text-align:center}
  .headline-box h2{font-family:'Arimo',Arial,sans-serif;font-weight:700;font-size:34px;line-height:1.08;color:var(--white);padding:0 6px 10px;text-shadow:0 1px 3px rgba(0,0,0,.6)}
  .headline-box p{background:var(--band-red);color:var(--white);font-size:22px;padding:7px 6px 8px}
  .content{position:absolute;top:443px;left:0;width:857px;padding:0 34px}
  .summary{font-size:14.5px;line-height:1.3;font-weight:700;margin-top:12px}
  .summary + .summary{margin-top:8px}
  .summary .campaign{color:var(--accent)}
  .call{text-align:center;margin-top:12px;font-size:17px;font-weight:700;line-height:1.25}
  .survey-link{text-align:center;font-size:24px;font-weight:700;margin-top:3px;line-height:1.2}
  .paper{text-align:center;font-size:16px;margin-top:8px;line-height:1.25}
  .website{text-align:center;font-size:30px;font-weight:700;margin-top:2px;line-height:1.2}
  .rule{height:2px;background:var(--white);opacity:.7;margin:8px 0 8px}
  .meeting-intro{text-align:center;font-size:16px;line-height:1.3}
  .meeting-date{text-align:center;font-size:23px;font-weight:700;margin-top:6px;line-height:1.2;color:var(--accent)}
  .interior-photo{position:absolute;top:868px;left:0;width:857px;height:246px;background:linear-gradient(180deg,#8a5030 0%,#5e2f1e 55%,#a06a44 100%)}
  .contact{position:absolute;top:1114px;left:0;width:857px;height:86px;background:var(--band-red);text-align:center;padding-top:12px}
  .contact p{font-size:17px;font-weight:700}
  .contact .line{font-size:24px;margin-top:4px}
  .contact .line small{font-size:17px;font-weight:400}
  .contact svg{vertical-align:-3px;margin:0 4px}
</style>
</head>
<body>
<main class="flyer">
  <header class="alarm"><h1>MAYDAY! MAYDAY!</h1></header>

  <div class="street-photo" role="img" aria-label="Photograph of The Heron pub frontage on a South Elmfield street"></div>
  <div class="headline-box">
    <h2>Safeguarding the future of the Heron</h2>
    <p>Protect pubs in South Elmfield</p>
  </div>

  <section class="content">
    <p class="summary">The Heron Pub is a Victorian building, five minutes walk from Elmfield Junction train station, which is in South Elmfield, South-East London, SE29. It was sold in 2014 and the new owner proceeded to gut the pub and convert it into seven flats.</p>
    <p class="summary">The Heron is an asset of community value, as awarded June 2015.</p>
    <p class="summary"><span class="campaign">SAVE THE HERON</span> is a campaign to protect the building and also raise money to lease the pub or buy the building. We want to open The Heron as a community co-op pub serving great good wine.</p>

    <p class="call">Please support our campaign by completing our survey at</p>
    <p class="survey-link">https://surveydock.com/58a1c7e04b29d6f3e10c7a2b</p>
    <p class="paper">Paper copies of the survey are available, get a friend or relative to check on</p>
    <p class="website">www.saveheron.org.uk</p>

    <div class="rule"></div>
    <p class="meeting-intro">Anyone wishing to find out more about our plans to open a great pub serving<br>fantastic food and drinks can attend our meeting on</p>
    <p class="meeting-date">18 August at 8 PM at the<br>Linden Tap, Marlow Road, SE29</p>
  </section>

  <div class="interior-photo" role="img" aria-label="Photograph of the pub's wood-panelled bar interior"></div>

  <footer class="contact">
    <p>You can contact us by emailing at:</p>
    <p class="line">saveheronse29@mailbox.org <small>or call us at</small>
      <svg width="20" height="20" viewBox="0 0 24 24" aria-hidden="true"><circle cx="12" cy="12" r="11" fill="none" stroke="#fff" stroke-width="2"/><path d="M8 6l2 0 1 3-1.5 1c.8 1.8 2 3 3.5 3.5l1-1.5 3 1 0 2c0 1-1 2-2 2-5 0-9-4-9-9 0-1 1-2 2-2z" fill="#fff"/></svg>2089640127</p>
  </footer>
</main>
</body>
</html>
```